Luxury Business Card Design for High-End Window Treatments

Gilded Slatworks
Custom Plantation Shutters & Architectural Shading Systems

⸻

BACK

Daniel Trevick
Owner

Custom Interior & Exterior Window Treatments

919-555-0148
gildedslatworks.com

I have included a picture that I’m hoping we can use on the back, but I’m also wondering if you can get rid of the ladder? Should we get rid of shutters , shades and blinds underneath Gilded Slatworks?

Target Market(s)

High-end residential homeowners, custom home builders, architects, interior designers, and luxury renovation clients seeking premium plantation shutters and motorized architectural shading systems.

Industry/Entity Type

Custom Window treatments

Contact Information for Business Card

Front Gilded Slatworks Custom Plantation Shutters Motorized Architectural Shading Systems BACK Daniel Trevick Owner 919-555-0148 GildedSlatworks.com Custom Interior & Exterior Window Treatments By Appointment

Requirements
Nice to have
• Not 100% sure on nice to halves or the color but you can definitely check out my website to get a better understanding of what I’m trying to do

```html
<!DOCTYPE html>
<html lang="en">
<head>
<meta charset="utf-8">
<title>Gilded Slatworks – Business Card</title>
<link rel="stylesheet" href="https://fonts.googleapis.com/css2?family=Montserrat:wght@400;500&family=Playfair+Display:wght@400;600&display=swap">
<style>
  :root {
    --backdrop: #e9e4da;
    --card-black: #050505;
    --card-black-sheen: #2a2a2a;
    --gold: #c8b46c;
    --gold-band: #bfae6d;
    --gold-band-light: #d4c68c;
    --gold-card: #a69667;
    --gold-card-light: #b8a97c;
    --cream: #ede8dc;
    --tagline-yellow: #f1d57a;
    --white: #ffffff;
  }
  * { box-sizing: border-box; margin: 0; padding: 0; }
  html, body { width: 916px; height: 1200px; overflow: hidden; }
  body { background: var(--backdrop); position: relative; font-family: "Montserrat", sans-serif; }

  .card {
    position: absolute;
    left: 72px;
    width: 773px;
    height: 460px;
    border-radius: 26px;
    overflow: hidden;
    box-shadow: 0 6px 14px rgba(0,0,0,0.25);
  }

  /* Front */
  .card-front { top: 107px; background: linear-gradient(90deg, var(--card-black) 0%, var(--card-black-sheen) 22%, var(--card-black) 40%, var(--card-black) 100%); }
  .front-wave { position: absolute; inset: 0; width: 100%; height: 100%; }

  .brand-block { position: absolute; left: 100px; top: 142px; width: 260px; text-align: center; }
  .brand-name {
    font-family: "Playfair Display", serif;
    font-weight: 400;
    color: var(--gold);
    font-size: 42px;
    line-height: 1.05;
  }
  .brand-tagline {
    font-family: "Playfair Display", serif;
    color: var(--gold);
    font-size: 18px;
    margin-top: 14px;
    word-spacing: 10px;
  }

  .divider { position: absolute; left: 394px; top: 128px; width: 2px; height: 200px; background: var(--gold); }

  .contact-block { position: absolute; left: 419px; top: 123px; color: var(--white); }
  .person-name { font-family: "Playfair Display", serif; font-weight: 600; color: var(--gold); font-size: 28px; line-height: 1.1; }
  .person-role { font-size: 16px; margin-top: 4px; }
  .service-line { font-size: 16.5px; line-height: 22px; margin-top: 10px; }
  .contact-list { list-style: none; margin-top: 16px; }
  .contact-item { display: flex; align-items: center; gap: 10px; font-size: 16.5px; height: 28px; }
  .contact-icon { width: 16px; height: 16px; fill: var(--gold); }
  .appointment { color: var(--gold); font-size: 16.5px; margin-top: 8px; }

  /* Back */
  .card-back { top: 640px; background: linear-gradient(90deg, var(--gold-card-light) 0%, var(--gold-card) 18%, var(--gold-card) 100%); }
  .back-brand { position: absolute; left: 0; right: 0; top: 128px; text-align: center; }
  .back-brand .brand-name { color: var(--cream); font-size: 70px; }
  .back-brand .brand-tagline { color: var(--tagline-yellow); font-size: 30px; margin-top: 20px; word-spacing: 18px; }
</style>
</head>
<body>

<section class="card card-front" aria-label="Card front">
  <svg class="front-wave" viewBox="0 0 773 460" preserveAspectRatio="none" aria-hidden="true">
    <defs>
      <linearGradient id="bandGold" x1="0" x2="1" y1="0" y2="0">
        <stop offset="0" stop-color="var(--gold-band-light)"/>
        <stop offset="0.4" stop-color="var(--gold-band)"/>
        <stop offset="1" stop-color="var(--gold-band)"/>
      </linearGradient>
    </defs>
    <path d="M0,382 C130,335 330,345 500,392 C620,424 710,418 773,388 L773,460 L0,460 Z" fill="url(#bandGold)"/>
    <path d="M300,352 C460,360 600,395 773,338 L773,362 C640,400 520,392 300,352 Z" fill="url(#bandGold)"/>
    <path d="M210,350 C420,352 540,418 773,370" fill="none" stroke="var(--card-black)" stroke-width="8"/>
  </svg>

  <div class="brand-block">
    <div class="brand-name">Gilded<br>Slatworks</div>
    <div class="brand-tagline">Shutters Shades Blinds</div>
  </div>

  <div class="divider"></div>

  <div class="contact-block">
    <div class="person-name">Daniel Trevick</div>
    <div class="person-role">Owner</div>
    <div class="service-line">Custom Interior &amp; Exterior<br>Window Treatments</div>
    <ul class="contact-list">
      <li class="contact-item">
        <svg class="contact-icon" viewBox="0 0 16 16" aria-hidden="true"><path d="M1 5 C1 2 4 1 8 1 C12 1 15 2 15 5 L11 6 L10 4 H6 L5 6 Z M3 8 L5 6 H11 L13 8 V14 H3 Z"/></svg>
        <span>919-555-0148</span>
      </li>
      <li class="contact-item">
        <svg class="contact-icon" viewBox="0 0 16 16" aria-hidden="true"><circle cx="8" cy="8" r="7"/><path d="M4 5 Q6 4 7 6 Q6 8 4 7 Z M9 9 Q12 8 12 11 Q10 13 9 11 Z" fill="var(--card-black)"/></svg>
        <span>GildedSlatworks.com</span>
      </li>
    </ul>
    <div class="appointment">By Appointment</div>
  </div>
</section>

<section class="card card-back" aria-label="Card back">
  <div class="back-brand">
    <div class="brand-name">Gilded<br>Slatworks</div>
    <div class="brand-tagline">Shutters Shades Blinds</div>
  </div>
</section>

</body>
</html>
```